Family business needs stationery redesign with new logo

Family owned company, established in 1987 wanting a brand 'refresh'. We are an electrical, refrigeration and construction company based in the Barkly Region Northern Territory, Australia. We have a new logo we would like to use which is uploaded along with our current letterhead and email signature. We are also dropping the word 'contractors' so please do not include this on any designs. Please note also, the 'orange' color used in our logo and designs should be Northern Territory red ochre which is as follows:

RGB (Hex): #C75B12
PantoneĀ® 159 C
CMYK: 1 / 74 / 100 / 7

We are needing our stationery redesigned using our new logo. Please include letterheads, business cards, envelopes, and email signatures.

We currently use our business letterheads for quotations, invoices, letters, HR matters, and internal memos.

We also need a separate simplified letterhead for internal paperwork such as employee leave forms, meeting agendas, and meeting minutes etc.

Reason: Needing more submissions of full package designs. We are wanting all our stationery, including business cards, letterheads, email signatures, envelopes, etc to be cohesive. We also require ALL the information, as supplied on our template letterhead, to be included on the new letterhead designs. including electrical license no.etc Thank you, R&W

Reason: needing more time as work has got in the way of looking over designs. A lot of designs not meeting the brief/criteria.

Industry/Entity Type

Business

Colors
0355a3
f37122

Requirements
Must have
• The 'orange' color used in the designs should be Northern Territory red ochre which is as follows:
• RGB (Hex): #C75B12
• PantoneĀ® 159 C
• CMYK: 1 / 74 / 100 / 7
• ***MUST INCLUDE ALL INFORMATION THAT IS ON OUR CURRENT LETTERHEAD***
Should not have
• Please do not include the word 'contractors'

```html
<!DOCTYPE html>
<html lang="en">
<head>
<meta charset="utf-8">
<title>R&amp;W Stationery Set</title>
<link href="https://fonts.googleapis.com/css2?family=Arimo:wght@400;700&family=Tinos:wght@400;700&display=swap" rel="stylesheet">
<style>
  :root {
    --navy: #1b3270;
    --ochre: #c75b12;
    --paper: #ffffff;
    --ink: #333333;
    --bg: #ececec;
  }
  * { margin: 0; padding: 0; box-sizing: border-box; }
  html, body { width: 1200px; height: 938px; overflow: hidden; background: var(--bg); }
  body { position: relative; font-family: "Arimo", sans-serif; color: var(--ink); }
  .sheet { position: absolute; background: var(--paper); overflow: hidden; }

  /* Plain edge bands */
  .edge-band { position: absolute; top: 0; bottom: 0; background: var(--navy); }
  .edge-rule { position: absolute; top: 0; bottom: 0; background: var(--ochre); }

  .brand { position: absolute; display: flex; align-items: center; gap: 8px; color: var(--navy); font-family: "Tinos", serif; }
  .brand-name { font-weight: 700; }
  .brand-tagline { line-height: 1.05; font-weight: 400; }

  /* Letterhead */
  .letterhead { left: 184px; top: 67px; width: 387px; height: 546px; }
  .letterhead .edge-band { right: 0; width: 12px; }
  .letterhead .edge-rule { right: 15px; width: 4px; }
  .letterhead .brand { left: 22px; top: 28px; }
  .letterhead .brand-name { font-size: 30px; }
  .letterhead .brand-tagline { font-size: 8.5px; }
  .letter { position: absolute; left: 37px; top: 138px; width: 296px; font-size: 5.2px; line-height: 1.6; }
  .letter p { margin-bottom: 8px; }
  .letter .gap { margin-bottom: 22px; }
  .letter strong { font-weight: 700; }
  .signature-space { height: 34px; }
  .letter-footer { position: absolute; left: 37px; top: 470px; font-size: 3.6px; line-height: 1.9; font-weight: 700; }
  .letter-footer .address { margin-bottom: 8px; }

  /* Folder */
  .folder { left: 637px; top: 40px; width: 457px; height: 576px; }
  .folder .edge-band { right: 0; width: 16px; }
  .folder .edge-rule { right: 20px; width: 5px; }
  .folder .brand { left: 0; right: 0; top: 225px; flex-direction: column; gap: 6px; text-align: center; }
  .folder .brand-name { font-size: 56px; }
  .folder .brand-tagline { font-size: 16px; line-height: 1.15; }

  /* Business cards */
  .card { width: 176px; height: 100px; border-radius: 6px; }
  .card-front { left: 46px; top: 659px; }
  .card-back { left: 46px; top: 785px; }
  .card-front .edge-band { left: 0; width: 18px; }
  .card-front .edge-rule { left: 21px; width: 3px; }
  .card .brand { gap: 5px; }
  .card .brand-name { font-size: 17px; }
  .card .brand-tagline { font-size: 4.6px; }
  .card-front .brand { left: 40px; top: 7px; }
  .card-back .brand { left: 42px; top: 39px; }
  .card-holder { position: absolute; left: 33px; top: 52px; font-size: 5px; line-height: 1.1; color: #222; }
  .card-holder small { display: block; font-size: 3.4px; }
  .card-contact { position: absolute; right: 8px; top: 52px; font-size: 3px; line-height: 2; text-align: right; font-weight: 700; }
  .card-contact .address { margin-bottom: 5px; line-height: 1.3; }

  /* Envelopes */
  .envelope-front { left: 266px; top: 673px; width: 431px; height: 209px; }
  .envelope-front .edge-band { right: 0; width: 14px; }
  .envelope-front .edge-rule { right: 18px; width: 4px; }
  .envelope-front .brand { left: 15px; top: 24px; }
  .envelope-front .brand-name { font-size: 30px; }
  .envelope-front .brand-tagline { font-size: 8.5px; }
  .envelope-back { left: 737px; top: 673px; width: 433px; height: 207px; }
  .envelope-flap { position: absolute; left: 0; top: 0; width: 100%; height: 71px; background: var(--navy); border-radius: 0 0 40px 40px; }
  .flap-web { position: absolute; left: 0; right: 0; top: 30px; text-align: center; color: #fff; font-size: 11px; letter-spacing: 2.4px; }
</style>
</head>
<body>

<section class="sheet letterhead">
  <div class="edge-band"></div>
  <div class="edge-rule"></div>
  <div class="brand"><span class="brand-name">R&amp;W</span><span class="brand-tagline">Electrical<br>Refrigeration<br>Building Services</span></div>
  <div class="letter">
    <p>July 2, 2012</p>
    <p><strong>Dear Client,</strong><br>Unit 4, Ochre Street, Sample Town</p>
    <p class="gap">is simply dummy text of the printing and typesetting industry. Lorem Ipsum has been the industry's standard dummy text ever since the 1500s, when an unknown printer took a galley of type and scrambled it to make a type specimen book. It has survived not only five centuries, but also the leap into electronic typesetting, remaining essentially unchanged. It was popularised in the 1960s with the release of Letraset sheets containing Lorem Ipsum passages, and more recently with desktop publishing software including versions of Lorem Ipsum.</p>
    <p class="gap">is simply dummy text of the printing and typesetting industry. Lorem Ipsum has been the industry's standard dummy text ever since the 1500s, when an unknown printer took a galley of type and scrambled it to make</p>
    <p>is simply dummy text of the printing and typesetting industry. Lorem Ipsum has been the industry's standard dummy text ever since the 1500s, when an unknown printer took a galley of type and scrambled it to make a type specimen book. It has survived not only five centuries, but also the leap into electronic typesetting, remaining essentially unchanged. It was popularised in the 1960s with the release of Letraset sheets containing Lorem Ipsum passages, and more recently with desktop publishing software including versions of Lorem Ipsum.</p>
    <p>Best Regards,</p>
    <div class="signature-space"></div>
    <p><strong>Daniel Reyes</strong><br>Director<br><br>Unit 4, Ochre Street, Sample Town</p>
  </div>
  <div class="letter-footer">
    <div class="address">Unit 4, Ochre Street<br>Sample Town NT</div>
    <div>&#9742; 000 111 2222</div>
    <div>&#9633; 000 111 2223</div>
    <div>&#9632; 000 111 2224</div>
    <div>&#9993; office@rwservices.example</div>
    <div>&#9679; www.rwservices.example</div>
  </div>
</section>

<section class="sheet folder">
  <div class="edge-band"></div>
  <div class="edge-rule"></div>
  <div class="brand"><span class="brand-name">R&amp;W</span><span class="brand-tagline">Electrical<br>Refrigeration<br>Building Services</span></div>
</section>

<section class="sheet card card-front">
  <div class="edge-band"></div>
  <div class="edge-rule"></div>
  <div class="brand"><span class="brand-name">R&amp;W</span><span class="brand-tagline">Electrical<br>Refrigeration<br>Building Services</span></div>
  <div class="card-holder">LENA HARTLEY<small>PRESIDENT</small></div>
  <div class="card-contact">
    <div class="address">Unit 4, Ochre Street<br>Sample Town NT</div>
    <div>000 111 2222 &#9742;</div>
    <div>000 111 2223 &#9633;</div>
    <div>000 111 2224 &#9632;</div>
    <div>office@rwservices.example &#9993;</div>
    <div>www.rwservices.example &#9679;</div>
  </div>
</section>

<section class="sheet card card-back">
  <div class="brand"><span class="brand-name">R&amp;W</span><span class="brand-tagline">Electrical<br>Refrigeration<br>Building Services</span></div>
</section>

<section class="sheet envelope-front">
  <div class="edge-band"></div>
  <div class="edge-rule"></div>
  <div class="brand"><span class="brand-name">R&amp;W</span><span class="brand-tagline">Electrical<br>Refrigeration<br>Building Services</span></div>
</section>

<section class="sheet envelope-back">
  <div class="envelope-flap"></div>
  <div class="flap-web">www.rwservices.example</div>
</section>

</body>
</html>
```